Nine Phase Ledger Roadmap Talk

I would like a flyer to hand out to participants at the speeches that we give. We are a CPA firm that specializes in entrepreneurs and realtors. We would like a flyer that looks crisp and clean, that integrates our logo and our company colors (shades of blue & gold). We would like the wording to be as laid out in the attached documents, but design is up to you. We would like a picture to go along with each point and are open to ideas. The flyer should be one page, preferably just the front.

Colors
3176b5
fee18a

Requirements
Must have
• Our logo and the wording supplied.
• A picture to go along with each topic.
Nice to have
• Images that pop, clean look, professional.
Should not have
• Look messy.

```html
<!DOCTYPE html>
<html lang="en">
<head>
<meta charset="utf-8">
<title>Nine Phase Ledger Roadmap Talk – Agenda Flyer</title>
<link rel="stylesheet" href="https://fonts.googleapis.com/css2?family=Open+Sans:wght@700;800&family=Lato:ital,wght@0,400;0,700;1,700&family=Arimo:wght@400&family=Libre+Baskerville:ital,wght@1,700&display=swap">
<style>
  :root {
    --brand-blue: #2f5ea8;
    --ring-blue: #5b8fcb;
    --title-grey: #8a8a8a;
    --body-grey: #4a4a4a;
    --gold: #d9ad3c;
    --paper: #f8f8f8;
    --icon-fill: #e3e8ef;
    --white: #ffffff;
  }
  * { margin: 0; padding: 0; box-sizing: border-box; }
  html, body { width: 894px; height: 1200px; overflow: hidden; }
  body { background: var(--paper); position: relative; font-family: "Arimo", Arial, sans-serif; }

  .title-block { position: absolute; left: 75px; top: 48px; }
  .title-main { font-family: "Open Sans", sans-serif; font-weight: 800; color: var(--brand-blue); font-size: 62px; line-height: 0.95; letter-spacing: -1px; }
  .title-sub { font-family: "Open Sans", sans-serif; font-weight: 700; color: var(--brand-blue); font-size: 36px; line-height: 1.05; margin-top: 6px; }
  .title-agenda { font-family: "Open Sans", sans-serif; font-weight: 800; color: var(--title-grey); font-size: 36px; line-height: 1.0; }

  .firm-mark { position: absolute; left: 570px; top: 86px; width: 280px; text-align: right; }
  .firm-name { font-family: "Lato", sans-serif; font-weight: 700; color: var(--brand-blue); font-size: 38px; line-height: 1; }
  .firm-tagline { font-family: "Libre Baskerville", serif; font-style: italic; font-weight: 700; font-size: 13px; color: #222; margin-top: 14px; }

  .timeline { position: absolute; left: 0; top: 0; }

  .step-text { position: absolute; font-size: 14px; line-height: 1.2; color: var(--body-grey); text-align: justify; }
  .step-text.left { left: 75px; width: 242px; }
  .step-text.right { left: 605px; width: 230px; }

  .closing-line { position: absolute; left: 0; width: 894px; top: 1040px; text-align: center; font-family: "Lato", sans-serif; font-style: italic; font-weight: 700; font-size: 26px; color: #1e1e1e; }

  .footer-band { position: absolute; left: 0; top: 1086px; width: 894px; height: 78px; background: var(--brand-blue); color: var(--white); text-align: center; font-family: "Lato", sans-serif; padding-top: 10px; }
  .footer-firm { font-size: 17px; font-weight: 700; }
  .footer-address { font-size: 13px; margin-top: 3px; }
  .footer-phones { font-size: 12.5px; margin-top: 4px; }
  .footer-phones span { margin: 0 12px; }

  .contact-row { position: absolute; left: 0; top: 1172px; width: 894px; text-align: center; font-family: "Lato", sans-serif; font-size: 12px; color: var(--brand-blue); }
  .contact-row span { margin: 0 12px; }
</style>
</head>
<body>

  <header class="title-block">
    <div class="title-main">NINE PHASE</div>
    <div class="title-sub">LEDGER ROADMAP</div>
    <div class="title-agenda">TALK<br>AGENDA</div>
  </header>

  <div class="firm-mark">
    <div class="firm-name">Steadfast Figures</div>
    <div class="firm-tagline">A Professional Accounting Corporation</div>
  </div>

  <svg class="timeline" width="894" height="1040" viewBox="0 0 894 1040" xmlns="http://www.w3.org/2000/svg">
    <g fill="none" stroke="var(--ring-blue)" stroke-width="4">
      <line x1="386" y1="228" x2="386" y2="328"/>
      <path d="M386 440 Q386 467 420 467 L474 467"/>
      <path d="M530 523 Q530 572 490 572 L442 572"/>
      <path d="M386 628 Q386 670 420 670 L474 670"/>
      <path d="M530 726 Q530 756 490 756 L442 756"/>
      <path d="M386 812 Q386 857 420 857 L474 857"/>
      <path d="M530 913 Q530 946 490 946 L442 946"/>
    </g>
    <circle cx="386" cy="228" r="11" fill="var(--ring-blue)"/>

    <g stroke="var(--ring-blue)" stroke-width="4" fill="var(--white)">
      <circle cx="386" cy="384" r="56"/>
      <circle cx="530" cy="467" r="56"/>
      <circle cx="386" cy="572" r="56"/>
      <circle cx="530" cy="670" r="56"/>
      <circle cx="386" cy="756" r="56"/>
      <circle cx="530" cy="857" r="56"/>
      <circle cx="386" cy="946" r="56"/>
    </g>

    <g fill="var(--icon-fill)">
      <circle cx="386" cy="384" r="34" role="img" aria-label="Icon of a dollar sign with scissors cutting a tax form"/>
      <circle cx="530" cy="467" r="34" role="img" aria-label="Icon of a hand holding a house with a dollar sign"/>
      <circle cx="386" cy="572" r="34" role="img" aria-label="Icon of a magnifying glass over a receipt"/>
      <circle cx="530" cy="670" r="34" role="img" aria-label="Icon of people meeting around a table with a check mark"/>
      <circle cx="386" cy="756" r="34" role="img" aria-label="Icon of a family with a piggy bank"/>
      <circle cx="530" cy="857" r="34" role="img" aria-label="Icon of a graduate in cap and gown"/>
      <circle cx="386" cy="946" r="34" role="img" aria-label="Icon of a growth chart with an upward arrow"/>
    </g>

    <g font-family="Lato, sans-serif" font-weight="700" font-size="15" fill="var(--white)" text-anchor="middle">
      <g fill="var(--ring-blue)" stroke="var(--white)" stroke-width="2">
        <circle cx="386" cy="440" r="12"/>
        <circle cx="530" cy="523" r="12"/>
        <circle cx="386" cy="628" r="12"/>
        <circle cx="474" cy="670" r="12"/>
        <circle cx="442" cy="756" r="12"/>
        <circle cx="474" cy="857" r="12"/>
        <circle cx="442" cy="946" r="12"/>
      </g>
      <text x="386" y="445">1</text>
      <text x="530" y="528">2</text>
      <text x="386" y="633">3</text>
      <text x="474" y="675">4</text>
      <text x="442" y="761">5</text>
      <text x="474" y="862">6</text>
      <text x="442" y="951">7</text>
    </g>
  </svg>

  <p class="step-text left" style="top:318px">We will first show you how to eliminate much of your self-employment tax on your return by converting your business into an S Corporation. A business owner making over $120,000 per year can save about $12,000 per year by doing this.</p>
  <p class="step-text right" style="top:418px">We will show you how to get tax free income from your corporation by renting you home to the corporation for the board meetings. Many of our clients are getting up to $21,000 in tax free income which could put $8,400 cash into your pocket.</p>
  <p class="step-text left" style="top:513px">We will show you the easiest way to track your expenses so that the only thing you will have to do to have rock solid books is to take a picture of the receipt and throw it away. It doesn't get any better than that.</p>
  <p class="step-text right" style="top:630px">Next, we show you the importance of tax planning and why it is critical to meet with your CPA before the end of the year and not just when you do your tax preparation.</p>
  <p class="step-text left" style="top:726px">We will show you how to hire your children and get $7,500 per child tax free. This will save you $3,000 per child in income tax reduction.</p>
  <p class="step-text right" style="top:810px">We will discuss how to make your child's college education tax deductible. With college cost spiraling out of control this is a biggie. Most of our clients have a savings of about $12,000 per year of college.</p>
  <p class="step-text left" style="top:890px">Our grand finale is to show you how to use, not one, but two corporations to get a several hundred thousand dollar tax deferral, get an interest free loan from the government and use that money to grow your business and your wealth.</p>

  <p class="closing-line">If they drive by with a machine gun you don't have to stand up.</p>

  <footer class="footer-band">
    <div class="footer-firm">STEADFAST FIGURES, A Professional Accounting Corporation</div>
    <div class="footer-address">820 N. Orchard Ave, Ste. B, Lodi Creek, CA 95000</div>
    <div class="footer-phones"><span>&#9742; 555-014-2270</span><span>Fax 555-014-2271</span></div>
  </footer>

  <div class="contact-row">
    <span>&#9993; Dana@steadfastfigures.com</span>
    <span>&#9993; Miles@steadfastfigures.com</span>
    <span>www.steadfastfiguresdemo.com</span>
  </div>

</body>
</html>
```